Coastline Premier Retreats Business Card Design

Design a business card for Coastline Premier Retreats. Look at the website for colors and reference. Card should have logo, name, title, office number, mobile number, email, URL and a tagline like, "Luxury Hotel & Resort Email Marketing" (This might change).

https://www.coastlinepremierretreats.example

The rest I will leave up to your imagination.

Contact Information for Business Card

Logo, name, title, office number, mobile number, email, URL and a tagline like, "Luxury Hotel & Resort Email Marketing" (This might change).

```html
<!DOCTYPE html>
<html lang="en">
<head>
<meta charset="utf-8">
<title>Coastline Premier Retreats – Business Card</title>
<link rel="stylesheet" href="https://fonts.googleapis.com/css2?family=Montserrat:wght@400;500;600;700&display=swap">
<style>
  :root {
    --page: #d9d9d9;
    --ink: #151515;
    --card-dark: #1b1b1b;
    --card-light: #ffffff;
    --accent: #f07a10;
    --text-dark: #222222;
    --text-light: #ffffff;
  }
  * { box-sizing: border-box; margin: 0; padding: 0; }
  html, body { width: 1200px; height: 901px; overflow: hidden; }
  body {
    background: var(--page);
    font-family: "Montserrat", sans-serif;
    display: flex;
    flex-direction: column;
    align-items: center;
    justify-content: center;
    gap: 44px;
  }
  .card {
    position: relative;
    width: 620px;
    height: 354px;
    border-radius: 22px;
    overflow: hidden;
    box-shadow: 0 6px 18px rgba(0,0,0,.25);
  }

  /* front */
  .card-front {
    background: var(--card-dark);
    display: flex;
    flex-direction: column;
    align-items: center;
    justify-content: center;
  }
  .brand {
    display: flex;
    align-items: center;
    gap: 12px;
    font-weight: 700;
    text-transform: uppercase;
    letter-spacing: .04em;
  }
  .brand-mark { background: var(--accent); display: block; }
  .card-front .brand { color: var(--text-light); font-size: 30px; }
  .card-front .brand-mark { width: 20px; height: 20px; }
  .tagline {
    margin-top: 58px;
    color: var(--accent);
    font-size: 19px;
    font-weight: 500;
    letter-spacing: .04em;
  }

  /* back */
  .card-back { background: var(--card-light); }
  .card-back .brand {
    position: absolute;
    left: 36px;
    top: 150px;
    width: 240px;
    color: var(--ink);
    font-size: 19px;
    line-height: 1.15;
  }
  .card-back .brand-mark { width: 14px; height: 14px; flex: none; }
  .divider {
    position: absolute;
    left: 290px;
    top: 70px;
    width: 1.5px;
    height: 190px;
    background: var(--accent);
  }
  .contact {
    position: absolute;
    left: 310px;
    top: 54px;
    color: var(--text-dark);
  }
  .person-name {
    color: var(--accent);
    font-size: 26px;
    font-weight: 700;
    letter-spacing: .03em;
    text-transform: uppercase;
    line-height: 1;
  }
  .person-title { font-size: 14px; margin-top: 4px; }
  .contact-list { list-style: none; margin-top: 16px; font-size: 12.5px; }
  .contact-list li { display: flex; align-items: center; gap: 9px; height: 22px; }
  .contact-list svg { width: 12px; height: 12px; fill: var(--accent); flex: none; }
  .address { margin-top: 12px; font-size: 12.5px; line-height: 1.45; padding-left: 21px; }
  .footer-band { position: absolute; left: 0; bottom: 0; }
  .footer-url {
    position: absolute;
    right: 24px;
    bottom: 18px;
    color: var(--text-light);
    font-size: 13px;
    letter-spacing: .02em;
    white-space: nowrap;
  }
  .footer-url span { color: var(--accent); }
</style>
</head>
<body>

  <section class="card card-front">
    <div class="brand"><i class="brand-mark"></i>Coastline Premier Retreats</div>
    <p class="tagline">Luxury Hotel &amp; Resort Email Marketing</p>
  </section>

  <section class="card card-back">
    <div class="brand"><i class="brand-mark"></i>Coastline Premier Retreats</div>
    <div class="divider"></div>

    <div class="contact">
      <h1 class="person-name">Daniel Reyes</h1>
      <p class="person-title">CEO/Founder</p>
      <ul class="contact-list">
        <li><svg viewBox="0 0 12 12" aria-hidden="true"><path d="M3 0h6a1 1 0 0 1 1 1v10a1 1 0 0 1-1 1H3a1 1 0 0 1-1-1V1a1 1 0 0 1 1-1zm0 1.5v8h6v-8z"/></svg>555.214.3800</li>
        <li><svg viewBox="0 0 12 12" aria-hidden="true"><path d="M0 4c1-2 11-2 12 0l-.5 1.5-2.5-.5V3.5H3V5l-2.5.5zM2.5 6.5 4 5h4l1.5 1.5V11h-7z"/></svg>+34 600 555 214</li>
        <li><svg viewBox="0 0 12 12" aria-hidden="true"><path d="M0 2h12v8H0zm1 1 5 4 5-4z"/></svg>info@coastlinepremierretreats.example</li>
      </ul>
      <p class="address">Po Box, 48 B Harbor Ln<br>North America, AB 10001</p>
    </div>

    <svg class="footer-band" width="620" height="354" viewBox="0 0 620 354" aria-hidden="true">
      <rect x="28" y="326" width="250" height="3" fill="var(--accent)"/>
      <path d="M282 354 V330 Q282 298 314 298 H620 V354 Z" fill="var(--ink)"/>
      <path d="M278 329 Q278 294 314 294" fill="none" stroke="var(--accent)" stroke-width="3"/>
    </svg>
    <p class="footer-url">www.<span>coastlinepremierretreats</span>.example</p>
  </section>

</body>
</html>
```